Flowy subpage design wanted for a modern tax/accounting firm in Switzerland

--- Introduction ---
We are a tax and accounting firm in Switzerland. We provide services for expats living in Switzerland, our service is quite exclusive and modern (digital).

We just relaunched our website www.fiscavantra.ch and are happy with the design, so the desired subpage (more details below) should of course fit in.

--- Main brief ---
Please see Word File attached. The page has to include the whole text (11 chapters). A very intuitive, flowy design on only one subpage (not one page per chapter) is a MUST. Also, it is key that the design is supporting the content of the individual chapters, so it would be advantageous if you'd have a good unterstanding of the text attached.

--- Further information ---
A similar example would be this one: https://www2.brennick.com/ch/en/pages/tax/articles/living-working-switzerland.html

This one is similar in what concerns the content, but NOT what we are looking for designwise. It is very simple and looks "thrown together", just not aesthetically pleasing in our opinion.

--- Final thoughts ---
- If you blow our minds with your design, we will certainly have future work for you.
- Our clients are between 20-50 years old, well educated, high income / high wealth, English speaking and living in Switzerland.
- CI/CD information:
Fonts
Montserrat regular / medium italic / bold
Colors
White #ffffffff
Darkblue #0a2b46
Darkblue 25% #b5bfc8
Darkblue 50% #8595a4
Greenblue #0d4261

We are looking forward to your designs!
Updates

Thank you very much for the submitted designs and your efforts. Unfortunately, none of the designs meet our expectations so far. Please note the following: - Designs that do not take CI into account will not be looked at more closely. - We have received many simple designs with very simple structure and accordion elements. But more important than the simple structure is an eye-catching design! Make it flowy and beautiful - We don't want pictures of Swiss vehicles, passes or other pictures that don't actively support the text. If you can make an illustration that really fits the context, fine, otherwise better leave it without. Thank you

Target Market(s)

Expats living in Switzerland. High income earners / high net worth individuals

Industry/Entity Type

tax/accounting

Number of Pages Required

1 page

Font styles to use
Other font styles liked:
• Montserrat

Colors
0054AA
0677BA
7BADD7
CADEEF
E8F1F8

Requirements
Must have
• based on general website design
Nice to have
• intuitive, flowy, attractive representation of much text
Should not have
• basic copy/paste of the text in sections :)

```html
<!DOCTYPE html>
<html lang="en">
<head>
<meta charset="utf-8">
<title>Living and working in Switzerland – Fiscavantra Advisory</title>
<link href="https://fonts.googleapis.com/css2?family=Montserrat:ital,wght@0,300;0,400;0,500;0,600;0,700;1,500&family=Cutive+Mono&display=swap" rel="stylesheet">
<style>
:root{
  --white:#ffffff;
  --darkblue:#0a2b46;
  --greenblue:#0d4261;
  --navy-hero:#1a3b5c;
  --blue-25:#b5bfc8;
  --blue-50:#8595a4;
  --text-blue:#2a5580;
  --link-blue:#3a6a98;
  --body-text:#3d4a57;
  --line:#dde3ea;
  --pale:#e8f1f8;
}
*{margin:0;padding:0;box-sizing:border-box}
html,body{width:1200px;height:977px;overflow:hidden;background:var(--white)}
body{position:relative;font-family:'Montserrat',sans-serif;color:var(--body-text)}
.abs{position:absolute}

/* header */
.site-header{left:0;top:0;width:1200px;height:63px;background:var(--white)}
.brand{left:130px;top:8px;display:flex;align-items:center;gap:8px}
.brand-dot{width:40px;height:40px;border-radius:50%;background:var(--darkblue)}
.brand-name{font-weight:600;font-size:16px;line-height:18px;color:var(--darkblue);letter-spacing:1px}
.main-nav{left:449px;top:25px;display:flex;gap:0;font-size:11.5px;color:var(--greenblue)}
.main-nav span{position:absolute;white-space:nowrap}
.nav-active{font-weight:600;color:var(--darkblue)}
.btn-calc{left:964px;top:17px;width:104px;height:32px;background:var(--greenblue);color:var(--white);font-size:11.5px;font-weight:500;display:flex;align-items:center;gap:10px;padding-left:10px}

/* hero */
.hero{left:0;top:63px;width:1200px;height:369px;background:linear-gradient(100deg,#16375a 0%,#1b3d5f 55%,#223f5c 75%,#1a3a5a 100%)}
.hero-title{left:144px;top:146px;font-size:43px;line-height:49px;color:var(--white);font-weight:500}
.hero-title .light{font-weight:400}
.hero-text{left:144px;top:266px;width:540px;font-size:11.4px;line-height:21.6px;color:#d7dfe8}

/* notes */
.note{background:var(--white);font-family:'Cutive Mono',monospace;color:#333;box-shadow:0 8px 30px rgba(10,43,70,.12)}
.note-chapters{left:685px;top:318px;width:260px;height:141px;padding:22px 0 0 27px;font-size:15px;line-height:23px}
.note-inner{left:907px;top:598px;width:259px;height:140px;padding:27px 0 0 27px;font-size:15px;line-height:23px}

/* breadcrumb */
.crumbs{left:143px;top:452px;font-size:10.8px;color:var(--link-blue)}
.crumbs .sep{margin:0 8px}
.crumb-line{left:0;top:482px;width:1113px;height:1px;background:var(--line)}
.burger{left:999px;top:453px;width:18px}
.burger i{display:block;height:2px;background:var(--link-blue);margin-bottom:5px}

/* intro */
.intro-title{left:0;width:1155px;top:548px;text-align:center;font-size:32px;font-weight:400;color:var(--text-blue)}
.intro-text{left:200px;width:770px;top:625px;text-align:center;font-size:12.4px;line-height:21px;color:var(--blue-50)}
.intro-bar{left:544px;top:694px;width:75px;height:4px;background:var(--greenblue)}

/* chapter */
.chapter-title{left:163px;top:733px;font-size:21.5px;color:var(--text-blue)}
.chapter-line{left:161px;top:775px;width:591px;height:1px;background:var(--blue-25)}
.topic-title{left:163px;top:795px;font-size:13px;font-weight:700;color:var(--text-blue)}
.topic-toggle{left:724px;top:801px;width:9px;height:2px;background:var(--text-blue)}
.body-copy{font-size:11px;line-height:16px;color:var(--body-text)}
.p1{left:163px;top:836px;width:595px}
.p2{left:163px;top:889px;width:345px}
.p3{left:163px;top:942px;width:345px}
.fact-card{left:519px;top:885px;width:224px;height:92px;background:linear-gradient(135deg,#e8f1f8,#cadeef);overflow:hidden}
.fact-text{left:25px;top:26px;font-size:14.5px;line-height:19px;color:var(--text-blue)}
.fact-text b{font-weight:600}
.fact-image{left:142px;top:10px;width:82px;height:82px;background:linear-gradient(160deg,#e24a3d,#c8261f)}

/* side nav */
.side-nav{left:806px;top:722px;width:237px;height:255px;border:1px solid var(--line);border-bottom:none}
.side-head{left:20px;top:17px;font-size:11.5px;color:var(--link-blue)}
.side-toggle{left:215px;top:25px;width:7px;height:2px;background:var(--link-blue)}
.side-rule{left:0;top:45px;width:235px;height:1px;background:var(--line)}
.side-list{left:20px;top:64px;list-style:none;font-size:10.5px;line-height:14px;color:var(--link-blue)}
.side-list li{position:relative;padding-left:19px;margin-bottom:14.5px;width:170px}
.side-list li::before{content:"";position:absolute;left:1px;top:6px;width:3px;height:3px;background:var(--link-blue)}
.side-list .current{font-weight:500;color:var(--greenblue)}
.side-bottom{left:20px;top:252px;width:200px;height:1px;background:var(--line)}
</style>
</head>
<body>

<header class="abs site-header">
  <div class="abs brand"><span class="brand-dot"></span><span class="brand-name">FISCAVANTRA<br>ADVISORY</span></div>
  <nav class="abs main-nav">
    <span class="nav-active" style="left:0">Home</span>
    <span style="left:59px">Tax returns</span>
    <span style="left:146px">More services ▾</span>
    <span style="left:257px">Swiss tax guide</span>
    <span style="left:369px">About us</span>
  </nav>
  <div class="abs btn-calc">
    <svg width="12" height="15" viewBox="0 0 12 15"><rect x="0.5" y="0.5" width="11" height="14" rx="1" fill="none" stroke="#fff"/><rect x="2.5" y="2.5" width="7" height="3" fill="#fff"/><g fill="#fff"><rect x="2.5" y="7" width="2" height="2"/><rect x="5" y="7" width="2" height="2"/><rect x="7.5" y="7" width="2" height="2"/><rect x="2.5" y="10.5" width="2" height="2"/><rect x="5" y="10.5" width="2" height="2"/><rect x="7.5" y="10.5" width="2" height="2"/></g></svg>
    Calculate
  </div>
</header>

<section class="abs hero" role="img" aria-label="Dark blue photograph of a city skyline with office towers">
  <svg class="abs" style="left:0;top:0" width="1200" height="369" viewBox="0 0 1200 369">
    <rect x="738" y="10" width="150" height="300" fill="#0f2c47" opacity=".35"/>
    <polygon points="0,301 403,351 0,369" fill="#dfe5ec"/>
    <polygon points="0,340 403,351 180,369 0,369" fill="#eef2f6"/>
    <polygon points="1200,250 1200,369 180,369 403,351" fill="#1b3d62"/>
  </svg>
</section>
<h1 class="abs hero-title">Living and working<br><span class="light">in Switzerland</span></h1>
<p class="abs hero-text">Lorem ipsum dolor sit amet, consectetur adipisicing elit, sed do eiusmod tempor incididunt ut labore et dolore magna aliqua. Ut enim ad minim veniam, quis nostrud exercitation ullamco laboris.</p>

<div class="abs crumbs">Home<span class="sep">›</span>Living amd working in switzerland</div>
<div class="abs crumb-line"></div>
<div class="abs burger"><i></i><i></i><i></i></div>

<div class="abs note note-chapters">Sub-menu for chapters.<br>Section fixed below main<br>menu, after scrolling.</div>
<svg class="abs" style="left:910px;top:474px" width="70" height="22" viewBox="0 0 70 22"><path d="M3 10 Q30 22 65 4" fill="none" stroke="#222" stroke-width="1"/><path d="M58 3 L65 4 L61 10" fill="none" stroke="#222" stroke-width="1"/></svg>

<svg class="abs" style="left:549px;top:523px" width="30" height="84" viewBox="0 0 30 84"><path d="M2 1 H25 V83" fill="none" stroke="#e3e9f0" stroke-width="3"/></svg>
<div class="abs" style="left:855px;top:564px;width:99px;height:1px;background:#eef1f4"></div>
<h2 class="abs intro-title">Life in Switzerland</h2>
<p class="abs intro-text">To give you a small impression of what to expect when living in Switzerland, we have put together some topics to make your new start in Switzerland as pleasant as possible.</p>
<div class="abs intro-bar"></div>

<h3 class="abs chapter-title">General</h3>
<div class="abs chapter-line"></div>
<h4 class="abs topic-title">4 official languages</h4>
<div class="abs topic-toggle"></div>
<p class="abs body-copy p1">Unlike many other countries in Europe, where there is usually only one official national language, Switzerland has four of them: German, French, Italian and Romansh.</p>
<p class="abs body-copy p2">The most widespread language is German, which is spoken mainly in central Switzerland and the cantons bordering Germany.</p>
<p class="abs body-copy p3">French dominates in the western part of Switzerland, and Italian in the southeastern part.</p>

<div class="abs fact-card">
  <p class="abs fact-text"><b>Official<br>documents</b><br>are generally<br>issued in</p>
  <div class="abs fact-image" role="img" aria-label="Photograph of a Swiss flag waving on a pole"></div>
</div>

<aside class="abs side-nav">
  <div class="abs side-head">General</div>
  <div class="abs side-toggle"></div>
  <div class="abs side-rule"></div>
  <ul class="abs side-list">
    <li>4 official languages</li>
    <li class="current">Currency and banking</li>
    <li>Public holidays</li>
    <li>Usual business and store opening hours</li>
    <li>Electricity and water</li>
    <li>Telephone and television</li>
  </ul>
  <div class="abs side-bottom"></div>
</aside>

<svg class="abs" style="left:830px;top:676px" width="58" height="52" viewBox="0 0 58 52"><path d="M52 3 Q20 12 7 47" fill="none" stroke="#222" stroke-width="1"/><path d="M3 40 L7 47 L13 42" fill="none" stroke="#222" stroke-width="1"/></svg>
<div class="abs note note-inner">Inner chapter navigation<br>on the left or right<br>side. It stays fixed<br>while scrolling.</div>

</body>
</html>
```